Harbor Crest Holdings Corporate Showcase

Provide an attractive Corporate Website for a boutique Investment Company to showcase our activities and corporate interests.

Our Company works across a number of Sectors including

Real Estate
E-Commerce
Healthcare
Beauty & Personal Care
Technology
Resources

Lets keep the personality

Modern
Global
Sophisticated
Calm
Interesting

Lets keep the pages with MINIMAL Words
Lets use Photos/ Imagery to tell the story

We'll need a Banner Menu -
About Us
Expertise
Global Outlook
Sectors
Management
Media
Contact Us

Many thanks
Best wishes
Dennis.

Target Market(s)

Investors
Clients

Coding

Coded - Design and coding required

Number of Pages Required

5+ page

Font styles to use
Sans Serif

Colors
886aae
3176b5
00a990
f68e4d
f04a50
e667a6

Requirements
Must have
• WordPress Coding

Checkout this Website for look and feel - its cool:
www.qvr-example.com

Harbor Crest Partners
(Harbor Crest Holdings LLP)
London
E9 4ZX
United Kingdom

www.HarborCrestPartners-example.com
Nice to have
• Sophisticated colour palette - black/ brown/ blue/ purple/

```html
<!DOCTYPE html>
<html lang="en">
<head>
<meta charset="utf-8">
<title>Harbor Crest Holdings</title>
<link href="https://fonts.googleapis.com/css2?family=Arimo:wght@400;700&family=Tinos:wght@400;700&display=swap" rel="stylesheet">
<style>
:root{
  --blue:#1f6fbd;
  --blue-dark:#17508a;
  --ink:#111111;
  --black:#000000;
  --text:#5b5b5b;
  --heading:#2b2b2b;
  --line:#555555;
  --orange:#f0c08e;
  --card:#eef4fb;
  --white:#ffffff;
  --divider:#d8d8d8;
}
*{box-sizing:border-box;margin:0;padding:0}
html,body{width:1200px;height:4175px;overflow:hidden;background:var(--white)}
body{font-family:"Arimo",Arial,sans-serif;color:var(--text)}
.page{position:relative;width:1200px;height:4175px;overflow:hidden}
.abs{position:absolute}
.serif{font-family:"Tinos","Times New Roman",serif}

/* header */
.site-header{left:0;top:0;width:1200px;height:122px;background:var(--black)}
.social-top{left:152px;top:26px;display:flex;gap:9px}
.social-top span{width:10px;height:10px;border-radius:50%;background:var(--white);display:block}
.brand{left:0;top:18px;width:1200px;text-align:center;color:var(--white);font-family:"Tinos",serif;font-weight:700;font-size:20px;letter-spacing:1px}
.header-tools{left:942px;top:24px;display:flex;align-items:center;gap:22px;color:var(--white);font-size:12px}
.header-tools .login{display:flex;align-items:center;gap:4px}
.main-nav{left:170px;top:62px;height:58px;display:flex;align-items:center;list-style:none}
.main-nav li{color:var(--white);font-weight:700;font-size:12.5px;padding:0 17px;height:58px;line-height:58px}
.main-nav li.active{background:var(--blue)}

/* hero */
.hero{left:0;top:122px;width:1200px;height:527px;background:radial-gradient(ellipse at 50% 40%,#1e3d66 0%,#0f2440 45%,#071324 100%)}
.hero-kicker{left:0;top:283px;width:1200px;text-align:center;color:var(--white);font-size:25px}
.hero-title{left:0;top:316px;width:1200px;text-align:center;color:var(--white);font-weight:700;font-size:45px;letter-spacing:.5px}
.hero-band{left:0;top:649px;width:1200px;height:6px;background:var(--blue)}

/* sectors */
.sectors{left:0;top:681px;width:1200px;height:130px}
.sector{position:absolute;top:0;width:200px;text-align:center}
.sector svg{display:block;margin:8px auto 0}
.sector p{margin-top:14px;font-weight:700;font-size:15.5px;color:#333;letter-spacing:.5px;line-height:25px}
.sector-divider{position:absolute;top:4px;width:1px;height:104px;background:var(--divider)}

/* shared */
.heading{font-family:"Tinos",serif;font-weight:700;color:var(--heading);line-height:1;letter-spacing:.5px}
.heading .accent{color:var(--blue)}
.body-copy{font-size:13.4px;line-height:24px;color:var(--text)}
.btn{display:flex;align-items:center;justify-content:center;gap:5px;font-weight:700;font-size:12.5px;letter-spacing:.3px}
.connector{background:var(--line)}
.photo{overflow:hidden}

/* about */
.about-title{left:110px;top:895px;font-size:41px;line-height:39px}
.about-copy{left:110px;top:990px;width:465px}
.btn-about{left:109px;top:1275px;width:176px;height:48px;border:2px solid var(--orange);color:#555}
.about-frame{left:613px;top:884px;width:491px;height:159px;background:var(--blue)}
.about-photo{left:629px;top:902px;width:458px;height:426px;background:linear-gradient(135deg,#c7b08c 0%,#e8dcc6 35%,#9aa7b8 60%,#3b4a5e 100%)}

/* global outlook */
.outlook-photo{left:0;top:1477px;width:600px;height:501px;background:linear-gradient(150deg,#3d5a80 0%,#8aa2bf 35%,#d7dee6 60%,#b35f5a 80%,#4d6a8c 100%)}
.outlook-box{left:600px;top:1571px;width:600px;height:501px;background:var(--blue)}
.outlook-title{left:673px;top:1676px;font-size:41px;color:var(--white)}
.outlook-copy{left:673px;top:1725px;width:470px;color:var(--white)}
.btn-outlook{left:671px;top:1918px;width:176px;height:48px;border:2px solid var(--white);color:var(--white)}

/* management */
.mgmt-title{left:0;top:2204px;width:1200px;text-align:center;font-size:40px}
.mgmt-card{top:2267px;width:470px;height:350px}
.mgmt-photo{position:absolute;left:0;top:0;width:470px;height:292px}
.mgmt-badge{position:absolute;right:0;top:160px;width:79px;height:78px;background:var(--blue);display:flex;align-items:center;justify-content:center}
.mgmt-panel{position:absolute;left:45px;top:238px;width:425px;height:112px;background:var(--white);padding:28px 0 0 32px}
.mgmt-panel h3{font-size:18.5px;font-weight:700;color:#222;letter-spacing:.3px}
.mgmt-panel p{margin-top:12px;font-size:13.2px;line-height:24px;color:#6a6a6a}

/* expertise */
.exp-frame{left:94px;top:2976px;width:474px;height:175px;background:var(--blue)}
.exp-photo{left:110px;top:2745px;width:458px;height:390px;background:linear-gradient(120deg,#5f6166 0%,#bfc4ca 35%,#eef0f2 60%,#c9b6a2 100%)}
.exp-title{left:628px;top:2737px;font-size:41px}
.exp-copy{left:628px;top:2796px;width:470px}
.btn-exp{left:626px;top:3081px;width:176px;height:48px;border:2px solid var(--blue);color:#555}

/* media */
.media-title{left:0;top:3280px;width:1200px;text-align:center;font-size:40px}
.media-card{top:3347px;width:308px;height:357px;background:var(--card)}
.media-card.raised{background:var(--white);box-shadow:0 4px 14px rgba(0,0,0,.12)}
.media-photo{width:308px;height:178px}
.media-body{padding:18px 0 0 32px}
.media-body h4{font-family:"Tinos",serif;font-weight:700;font-size:15.5px;color:#333}
.media-date{margin-top:6px;font-size:12px;color:var(--blue);display:flex;align-items:center;gap:4px}
.media-body p{margin-top:8px;font-size:11.5px;line-height:26px;color:#777;width:250px}
.media-share{margin-top:10px;display:flex;gap:8px}
.media-share span{width:21px;height:21px;border-radius:50%;border:1.5px solid #666;display:block}

/* footer */
.footer-band{left:0;top:3795px;width:1200px;height:5px;background:var(--blue)}
.site-footer{left:0;top:3800px;width:1200px;height:375px;background:var(--ink)}
.contact-item{position:absolute;top:3847px;width:260px;text-align:center;color:var(--white);font-size:15px;font-weight:700;line-height:24px}
.contact-icon{width:60px;height:60px;border-radius:50%;border:2px solid var(--white);background:var(--blue);margin:0 auto 18px;display:flex;align-items:center;justify-content:center}
.footer-rule{left:110px;top:4017px;width:978px;height:1px;background:#444}
.copyright{left:0;top:4052px;width:1200px;text-align:center;color:var(--white);font-size:15px}
.footer-social{left:520px;top:4077px;display:flex;gap:6px}
.footer-social span{width:38px;height:38px;border-radius:50%;border:2px solid var(--white);display:block}
</style>
</head>
<body>
<div class="page">

  <!-- header -->
  <header class="abs site-header"></header>
  <div class="abs social-top" aria-label="Social links"><span></span><span></span><span></span><span></span></div>
  <div class="abs brand">HARBOR CREST HOLDINGS</div>
  <div class="abs header-tools">
    <svg width="13" height="13" viewBox="0 0 14 14"><circle cx="6" cy="6" r="4.5" fill="none" stroke="#fff" stroke-width="2"/><line x1="9.3" y1="9.3" x2="13" y2="13" stroke="#fff" stroke-width="2"/></svg>
    <span class="login"><svg width="10" height="12" viewBox="0 0 10 12"><circle cx="5" cy="3" r="2.8" fill="#fff"/><path d="M0 12 Q0 6 5 6 Q10 6 10 12Z" fill="#fff"/></svg>LOG IN</span>
  </div>
  <ul class="abs main-nav">
    <li class="active">HOME</li><li>ABOUT US</li><li>EXPERTISE</li><li>GLOBAL OUTLOOK</li><li>SECTORS</li><li>MANAGEMENT</li><li>MEDIA</li><li>CONTACT US</li>
  </ul>

  <!-- hero -->
  <section class="abs hero" role="img" aria-label="Dark blue toned photo of luxury handbags, gloves and jewellery"></section>
  <div class="abs hero-kicker serif">WE ARE</div>
  <div class="abs hero-title serif">BOUTIQUE INVESTMENT COMPANY</div>
  <svg class="abs" style="left:570px;top:391px" width="60" height="60" viewBox="0 0 60 60"><circle cx="30" cy="30" r="27" fill="none" stroke="#fff" stroke-width="3"/><path d="M24 18 L42 30 L24 42Z" fill="#fff"/></svg>
  <svg class="abs" style="left:44px;top:322px" width="22" height="34" viewBox="0 0 22 34"><path d="M18 3 L5 17 L18 31" fill="none" stroke="#fff" stroke-width="4"/></svg>
  <svg class="abs" style="left:1133px;top:322px" width="22" height="34" viewBox="0 0 22 34"><path d="M4 3 L17 17 L4 31" fill="none" stroke="#fff" stroke-width="4"/></svg>
  <div class="abs hero-band"></div>

  <!-- sectors -->
  <section class="abs sectors">
    <div class="sector" style="left:0">
      <svg width="60" height="60" viewBox="0 0 60 60" fill="none" stroke="#1f4f80" stroke-width="2"><rect x="8" y="10" width="24" height="44"/><rect x="32" y="28" width="20" height="26"/><path d="M12 16h4M20 16h4M12 24h4M20 24h4M12 32h4M20 32h4M36 34h4M44 34h4M36 42h4M44 42h4" stroke="#2c8bd6"/><path d="M4 54h52"/></svg>
      <p>REAL ESTATE</p>
    </div>
    <div class="sector-divider" style="left:200px"></div>
    <div class="sector" style="left:199px">
      <svg width="60" height="60" viewBox="0 0 60 60" fill="none" stroke="#1f4f80" stroke-width="2"><rect x="6" y="8" width="48" height="34" rx="2"/><path d="M24 42v8h12v-8M18 52h24"/><path d="M17 17h5l4 13h12l3-9H24" stroke="#2c8bd6"/><circle cx="28" cy="35" r="2" stroke="#2c8bd6"/><circle cx="36" cy="35" r="2" stroke="#2c8bd6"/></svg>
      <p>E-COMMERCE</p>
    </div>
    <div class="sector-divider" style="left:399px"></div>
    <div class="sector" style="left:399px">
      <svg width="60" height="60" viewBox="0 0 60 60" fill="none" stroke="#1f4f80" stroke-width="2"><path d="M6 42c8-6 14-6 20-2h10c3 0 3 4 0 4H26M6 52l8-6h20l16-12c3-2 5 1 3 3L36 52"/><path d="M14 24h6l3-7 4 13 3-6h8" stroke="#2c8bd6"/><circle cx="46" cy="14" r="7" stroke="#2c8bd6"/><path d="M46 10v8M42 14h8" stroke="#2c8bd6"/></svg>
      <p>HEALTHCARE</p>
    </div>
    <div class="sector-divider" style="left:598px"></div>
    <div class="sector" style="left:599px">
      <svg width="60" height="60" viewBox="0 0 60 60" fill="none" stroke="#1f4f80" stroke-width="2"><path d="M30 6c-10 0-16 8-16 18v26M30 6c10 0 16 8 16 18v26"/><path d="M10 56c4-10 12-14 20-14s16 4 20 14"/><path d="M30 16l2 5 5 1-5 2-2 5-2-5-5-2 5-1z" stroke="#2c8bd6"/><path d="M46 8l1 3 3 1-3 1-1 3-1-3-3-1 3-1z" stroke="#2c8bd6"/></svg>
      <p>BEAUTY &amp;<br>PERSONAL CARE</p>
    </div>
    <div class="sector-divider" style="left:798px"></div>
    <div class="sector" style="left:799px">
      <svg width="60" height="60" viewBox="0 0 60 60" fill="none" stroke="#1f4f80" stroke-width="2"><circle cx="30" cy="30" r="22"/><circle cx="30" cy="30" r="13" stroke="#2c8bd6"/><circle cx="30" cy="30" r="5" stroke="#2c8bd6"/><path d="M30 4v6M30 50v6M4 30h6M50 30h6M11 11l4 4M45 45l4 4M49 11l-4 4M15 45l-4 4"/></svg>
      <p>TECHNOLOGY</p>
    </div>
    <div class="sector-divider" style="left:999px"></div>
    <div class="sector" style="left:999px">
      <svg width="60" height="60" viewBox="0 0 60 60" fill="none" stroke="#1f4f80" stroke-width="2"><circle cx="34" cy="24" r="16"/><circle cx="34" cy="24" r="7" stroke="#2c8bd6"/><path d="M34 12v4M34 32v4M22 24h4M42 24h4" stroke="#2c8bd6"/><path d="M22 36L8 50l4 4 14-14"/></svg>
      <p>RESOURCES</p>
    </div>
  </section>

  <!-- about -->
  <h2 class="abs heading about-title">ABOUT <span class="accent">HARBOR CREST<br>HOLDINGS</span></h2>
  <div class="abs about-copy body-copy">
    <p>Lorem ipsum dolor sit amet, consectetur adipiscing elit, sed do eiusmod tempor incididunt ut labore et dolore magna aliqua. Ut enim ad minim veniam, quis nostrud exercitation ullamco laboris nisi ut aliquip ex ea commodo consequat. Duis aute irure dolor in reprehenderit in voluptate velit esse cillum dolore eu fugiat nulla pariatur. Excepteur sint occaecat cupidatat non proident, sunt in culpa qui officia deserunt mollit anim id est laborum.</p>
    <p style="margin-top:24px">Lorem ipsum dolor sit amet, consectetur adipiscing elit, sed do eiusmod tempor incididunt ut labore et dolore magna aliqua. Ut enim ad minim veniam, quis nostrud exercitation ullamco laboris</p>
  </div>
  <div class="abs btn btn-about">LEARN MORE <span>&#10230;</span></div>
  <div class="abs about-frame"></div>
  <div class="abs photo about-photo" role="img" aria-label="Overhead photo of a business team shaking hands over a desk with charts and a laptop"></div>

  <div class="abs connector" style="left:845px;top:1328px;width:2px;height:91px"></div>
  <div class="abs connector" style="left:281px;top:1417px;width:566px;height:2px"></div>
  <div class="abs connector" style="left:281px;top:1417px;width:2px;height:57px"></div>

  <!-- global outlook -->
  <div class="abs photo outlook-photo" role="img" aria-label="Photo of colleagues reviewing financial charts on a table"></div>
  <div class="abs outlook-box"></div>
  <h2 class="abs heading outlook-title">GLOBAL OUTLOOK</h2>
  <p class="abs outlook-copy body-copy">Lorem ipsum dolor sit amet, consectetur adipiscing elit, sed do eiusmod tempor incididunt ut labore et dolore magna aliqua. Ut enim ad minim veniam, quis nostrud exercitation ullamco laboris nisi ut aliquip ex ea commodo consequat. Duis aute irure dolor in reprehenderit in voluptate velit esse cillum dolore eu fugiat nulla pariatur. Excepteur sint occaecat cupidatat non proident, sunt in culpa qui officia deserunt mollit anim id est laborum.</p>
  <div class="abs btn btn-outlook">LEARN MORE <span>&#10230;</span></div>

  <div class="abs connector" style="left:879px;top:2072px;width:2px;height:66px"></div>
  <div class="abs connector" style="left:599px;top:2136px;width:282px;height:2px"></div>
  <div class="abs connector" style="left:599px;top:2136px;width:2px;height:50px"></div>

  <!-- management -->
  <h2 class="abs heading mgmt-title">MANAGEMENT</h2>
  <article class="abs mgmt-card" style="left:110px">
    <div class="mgmt-photo photo" role="img" aria-label="Photo of three colleagues in a meeting at a laptop" style="background:linear-gradient(120deg,#7a5a48 0%,#c9b9a8 40%,#e8eaee 70%,#8c9099 100%)"></div>
    <div class="mgmt-badge"><svg width="44" height="44" viewBox="0 0 44 44" fill="none" stroke="#fff" stroke-width="2"><circle cx="22" cy="22" r="14"/><path d="M22 4v5M22 35v5M4 22h5M35 22h5M9 9l4 4M31 31l4 4M35 9l-4 4M13 31l-4 4"/><circle cx="22" cy="19" r="3"/><path d="M16 29c1-4 3-6 6-6s5 2 6 6"/></svg></div>
    <div class="mgmt-panel"><h3>LOREM IPSUM DOLOR SIT AMET</h3><p>Sed ut perspiciatis unde omnis iste natus error sit voluptatem accusantium doloremque lauda</p></div>
  </article>
  <article class="abs mgmt-card" style="left:619px">
    <div class="mgmt-photo photo" role="img" aria-label="Photo of a businessman in glasses reading at his desk" style="background:linear-gradient(120deg,#3c3f47 0%,#9aa3ad 45%,#dfe5ea 75%,#c4a27a 100%)"></div>
    <div class="mgmt-badge"><svg width="44" height="44" viewBox="0 0 44 44" fill="none" stroke="#fff" stroke-width="2"><circle cx="22" cy="22" r="14"/><path d="M22 4v5M22 35v5M4 22h5M35 22h5M9 9l4 4M31 31l4 4M35 9l-4 4M13 31l-4 4"/><path d="M16 22l4 4 8-8"/></svg></div>
    <div class="mgmt-panel"><h3>LOREM IPSUM DOLOR SIT AMET</h3><p>Sed ut perspiciatis unde omnis iste natus error sit voluptatem accusantium doloremque lauda</p></div>
  </article>

  <div class="abs connector" style="left:596px;top:2591px;width:2px;height:98px"></div>
  <div class="abs connector" style="left:596px;top:2687px;width:117px;height:2px"></div>
  <div class="abs connector" style="left:711px;top:2687px;width:2px;height:37px"></div>

  <!-- expertise -->
  <div class="abs exp-frame"></div>
  <div class="abs photo exp-photo" role="img" aria-label="Photo of a man writing notes beside a laptop"></div>
  <h2 class="abs heading exp-title">EXPERTISE</h2>
  <div class="abs exp-copy body-copy">
    <p>Lorem ipsum dolor sit amet, consectetur adipiscing elit, sed do eiusmod tempor incididunt ut labore et dolore magna aliqua. Ut enim ad minim veniam, quis nostrud exercitation ullamco laboris nisi ut aliquip ex ea commodo consequat. Duis aute irure dolor in reprehenderit in voluptate velit esse cillum dolore eu fugiat nulla pariatur. Excepteur sint occaecat cupidatat non proident, sunt in culpa qui officia deserunt mollit anim id est laborum.</p>
    <p style="margin-top:17px">Lorem ipsum dolor sit amet, consectetur adipiscing elit, sed do eiusmod tempor incididunt ut labore et dolore magna aliqua. Ut enim ad minim veniam, quis nostrud exercitation ullamco laboris</p>
  </div>
  <div class="abs btn btn-exp">LEARN MORE <span>&#10230;</span></div>

  <div class="abs connector" style="left:599px;top:3156px;width:2px;height:104px"></div>

  <!-- media -->
  <h2 class="abs heading media-title">OUR <span class="accent">MEDIA</span></h2>
  <article class="abs media-card" style="left:112px">
    <div class="media-photo photo" role="img" aria-label="Photo of a business team meeting around a table" style="background:linear-gradient(120deg,#e9e6e2 0%,#8b7b70 40%,#3d4552 70%,#d9dde2 100%)"></div>
    <div class="media-body"><h4>Lorem ipsum dolor sit amet</h4><div class="media-date">&#9719; Jan 20, 2020</div><p>Lorem ipsum dolor sit amet, consectetur adipiscing elit, sed do eiusmod</p><div class="media-share"><span></span><span></span><span></span><span></span></div></div>
  </article>
  <article class="abs media-card raised" style="left:446px">
    <div class="media-photo photo" role="img" aria-label="Photo of hands pointing at printed financial charts" style="background:linear-gradient(130deg,#1f2f45 0%,#4b6a8c 40%,#a8c2d8 70%,#2b3a4f 100%)"></div>
    <div class="media-body"><h4>Lorem ipsum dolor sit amet</h4><div class="media-date">&#9719; Jan 20, 2020</div><p>Lorem ipsum dolor sit amet, consectetur adipiscing elit, sed do eiusmod</p><div class="media-share"><span></span><span></span><span></span><span></span></div></div>
  </article>
  <article class="abs media-card" style="left:780px">
    <div class="media-photo photo" role="img" aria-label="Photo of two people signing documents at a desk" style="background:linear-gradient(120deg,#6a4a5a 0%,#c9b3c0 40%,#eceaf0 70%,#8e7d96 100%)"></div>
    <div class="media-body"><h4>Lorem ipsum dolor sit amet</h4><div class="media-date">&#9719; Jan 20, 2020</div><p>Lorem ipsum dolor sit amet, consectetur adipiscing elit, sed do eiusmod</p><div class="media-share"><span></span><span></span><span></span><span></span></div></div>
  </article>

  <!-- footer -->
  <div class="abs footer-band"></div>
  <footer class="abs site-footer"></footer>
  <div class="contact-item" style="left:225px">
    <div class="contact-icon"><svg width="20" height="26" viewBox="0 0 20 26"><path d="M10 1C5 1 1 5 1 10c0 7 9 15 9 15s9-8 9-15c0-5-4-9-9-9z" fill="#fff"/><circle cx="10" cy="10" r="3.5" fill="#1f6fbd"/></svg></div>
    123, Lorem ipsum dolor sit<br>amet, consectetur
  </div>
  <div class="contact-item" style="left:465px">
    <div class="contact-icon"><svg width="22" height="22" viewBox="0 0 24 24"><path d="M6.6 10.8a15 15 0 006.6 6.6l2.2-2.2c.3-.3.7-.4 1-.2 1.1.4 2.3.6 3.6.6.6 0 1 .4 1 1V20c0 .6-.4 1-1 1A17 17 0 013 4c0-.6.4-1 1-1h3.5c.6 0 1 .4 1 1 0 1.3.2 2.5.6 3.6.1.3 0 .7-.2 1z" fill="#fff"/></svg></div>
    Phone:<br>+1 555 014 2290
  </div>
  <div class="contact-item" style="left:697px">
    <div class="contact-icon"><svg width="24" height="18" viewBox="0 0 24 18"><rect x="1" y="1" width="22" height="16" rx="2" fill="#fff"/><path d="M2 3l10 7 10-7" fill="none" stroke="#1f6fbd" stroke-width="2"/></svg></div>
    Email:<br>info@harborcrest-example.com
  </div>
  <div class="abs footer-rule"></div>
  <div class="abs copyright">&copy; 2020 Harbor Crest Holdings | All Rights Reserved</div>
  <div class="abs footer-social" aria-label="Social links"><span></span><span></span><span></span><span></span></div>

</div>
</body>
</html>
```